Birch And Harbor Website A Website design for book editing

A website design for book editing

Our proofreading, editing and manuscript review packages are specifically tailored to help you publish the best possible version of your story.

NEED HELP PUBLISHING A BESTSELLER?

If you’re looking for professional book editing services from senior publishing industry insiders, look no further. Besides editing, we can also answer all your publishing questions and get you started building your author platform.

OUR SERVICES

We've carefully structured our packages to maximize value for every budget.

PRICING

$.02
PER WORD
Proofreading
Line Edit (Copy-editing)
Fix spelling and grammar
Sales copy/summary revision

$.04
PER WORD
Proofreading
Line Edit (Copy-editing)
Fix spelling and grammar
Organization and content
Plot and pacing
Manuscript Review

$.06
PER WORD
Proofreading
Line Edit (Copy-editing)
Fix spelling and grammar
Organization and content
Plot and pacing
Manuscript Review
Formatting (print and ebook)
Pre-publication proofread

OUR PROCESS

Send us a sample of your book. Our caffeine-fueled, eagle-eyed editors will go through it and then email you with their comments and suggestions. You can ask them any questions you want. They will look for…

Typos and grammatical errors.
Spelling and word choice issues
Punctuation and style
Word choice, clarity and flow.
Sentence structure and craft
If your writing is already clean, then they’ll discuss bigger picture things with you, like theme, concept, purpose, audience, potential market and branding (including title, subtitle, and tagline or elevator pitch).

Once you feel comfortable and confident in an editor’s expertise, skill and knowledge, and are ready to move ahead, we’ll send an invoice for the first half of the total word count so the editor can get started. We’ll charge the rest when the project is close to completion.

Target Market(s)

Authors

Industry/Entity Type

Book Publisher

Coding

Coded - Design and coding required

Number of Pages Required

1 page

Requirements
Must have
• OUR SERVICES
• We've carefully structured our packages to maximize value for every budget.
• PRICING
• $.02
• PER WORD
• Proofreading
• Line Edit (Copy-editing)
• Fix spelling and grammar
• Sales copy/summary revision
• $.04
• PER WORD
• Proofreading
• Organization and content
• Plot and pacing
• Manuscript Review
• $.06
• PER WORD
• Proofreading
• Plot and pacing
• Manuscript Review
• Formatting (print and ebook)
• Pre-publication proofread

```html
<!DOCTYPE html>
<html lang="en">
<head>
<meta charset="utf-8">
<title>Birch And Harbor — Book Editing</title>
<link href="https://fonts.googleapis.com/css2?family=Open+Sans:wght@400;600;700;800&display=swap" rel="stylesheet">
<style>
:root{
  --red:#e3101c;
  --red-dark:#b00812;
  --ink:#1b1b1b;
  --text:#333333;
  --muted:#666666;
  --line:#dddddd;
  --paper:#ffffff;
  --mist:#eeeeee;
  --footer:#1c1c1c;
  --footer-text:#bbbbbb;
}
*{margin:0;padding:0;box-sizing:border-box}
html,body{width:1200px;height:3939px;overflow:hidden}
body{position:relative;background:var(--paper);font-family:"Open Sans",Arial,sans-serif;color:var(--text)}
.accent{color:var(--red)}

/* header */
.site-header{position:absolute;left:0;top:0;width:1200px;height:100px}
.brand{position:absolute;font-weight:700;color:var(--red);font-size:24px;letter-spacing:-.3px;display:flex;align-items:center;gap:8px}
.brand .dot{width:12px;height:12px;background:var(--red);border-radius:50%}
.site-header .brand{left:158px;top:36px}
.main-nav{position:absolute;top:42px;left:0;width:1200px;font-size:15px;color:var(--ink)}
.main-nav a{position:absolute;color:inherit;text-decoration:none}

/* hero */
.hero{position:absolute;left:0;top:100px;width:1200px;height:533px;
  background:linear-gradient(100deg,#6b4a33 0%,#9b7454 30%,#b48f6e 55%,#8f6a4c 80%,#5e412c 100%)}
.hero-panel{position:absolute;left:163px;top:89px;width:320px;height:320px;background:var(--red);padding:58px 0 0 36px}
.hero-panel h1{color:#fff;font-size:32px;line-height:44px;font-weight:800}
.btn-outline{position:absolute;left:39px;top:220px;width:150px;height:45px;border:2px solid #fff;border-radius:23px;color:#fff;font-size:11px;font-weight:700;display:flex;align-items:center;justify-content:center}
.hero-arrow{position:absolute;top:250px;width:32px;height:32px;border:2px solid rgba(255,255,255,.8);border-radius:50%}
.hero-dots{position:absolute;left:568px;top:490px;display:flex;gap:10px}
.hero-dots span{width:11px;height:11px;border-radius:50%;background:#fff}
.hero-dots span.on{background:var(--red)}

/* intro */
.intro{position:absolute;left:345px;top:694px;width:510px;text-align:center;font-size:17px;line-height:34px;color:var(--ink)}
.ornament{position:absolute;left:548px;width:104px;height:14px;border-radius:7px;
  background:radial-gradient(ellipse at center,rgba(227,16,28,.55) 0%,rgba(227,16,28,.2) 55%,rgba(227,16,28,0) 100%)}
.rule{position:absolute;left:163px;top:927px;width:874px;height:1px;background:var(--line)}

/* services */
.services-title{position:absolute;left:163px;top:1030px;font-size:32px;font-weight:700;color:var(--ink)}
.services-lead{position:absolute;left:163px;top:1090px;width:245px;font-size:16px;line-height:30px;color:var(--text)}
.service-card{position:absolute;width:273px;height:212px;background:#fff;box-shadow:0 2px 10px rgba(0,0,0,.18);text-align:center;padding-top:36px}
.service-card svg{width:64px;height:64px}
.service-card p{font-size:16px;font-weight:700;line-height:26px;color:var(--ink);margin-top:14px}

/* pricing */
.pricing{position:absolute;left:0;top:1539px;width:1200px;height:811px;
  background:radial-gradient(ellipse at 50% 35%,#ffffff 0%,#ececec 55%,#d9d9d9 100%)}
.pricing h2{position:absolute;top:70px;width:1200px;text-align:center;font-size:30px;font-weight:600;color:var(--ink)}
.plan{position:absolute;top:160px;width:255px;height:551px;background:#fff;box-shadow:0 2px 8px rgba(0,0,0,.2)}
.plan-head{height:147px;background:linear-gradient(160deg,#000 0%,#1a0204 40%,#8e0610 70%,var(--red) 100%);color:#fff;text-align:center;padding-top:22px}
.plan-price{font-size:54px;font-weight:700;line-height:64px}
.plan-unit{font-size:12px;font-weight:700;margin-top:14px;letter-spacing:.5px}
.plan ul{list-style:none}
.plan li{height:35px;border-bottom:1px solid var(--line);font-size:13px;display:flex;align-items:center;justify-content:center;color:var(--ink)}
.btn-red{position:absolute;left:68px;top:494px;width:120px;height:31px;border-radius:16px;background:var(--red);color:#fff;font-size:12px;font-weight:700;display:flex;align-items:center;justify-content:center}

/* how it works */
.how-title{position:absolute;top:2412px;width:1200px;text-align:center;font-size:32px;font-weight:700;color:var(--ink)}
.step{position:absolute;top:2510px;width:274px;text-align:center}
.step-photo{height:174px}
.step h3{font-size:14px;font-weight:700;color:var(--red);margin-top:24px}
.step p{font-size:13px;line-height:26px;color:var(--muted);margin:12px auto 0;width:240px}

/* process */
.process-frame{position:absolute;left:176px;top:2994px;width:417px;height:446px;border:2px solid var(--red)}
.process-photo{position:absolute;left:163px;top:2980px;width:415px;height:447px;background:linear-gradient(135deg,#3b3b3b,#8c8a86 50%,#d9d6d0)}
.process-title{position:absolute;left:625px;top:2992px;font-size:32px;font-weight:700;color:var(--ink)}
.process-copy{position:absolute;left:625px;top:3060px;width:450px;font-size:13px;line-height:24px;color:var(--muted)}
.process-copy p+p{margin-top:24px}

/* call band */
.call-band{position:absolute;left:0;top:3529px;width:1200px;height:100px;background:var(--red);color:#fff;font-size:22px;display:flex;align-items:center;justify-content:center;gap:14px}

/* footer */
.site-footer{position:absolute;left:0;top:3629px;width:1200px;height:310px;background:var(--footer);color:var(--footer-text)}
.site-footer .brand{left:163px;top:82px;color:#fff;font-size:20px}
.site-footer .brand .dot{background:#fff}
.social{position:absolute;left:166px;top:134px;display:flex;gap:22px}
.social span{width:9px;height:9px;border-radius:50%;background:#fff}
.foot-col{position:absolute;top:64px;font-size:12px}
.foot-col h4{color:#fff;font-size:13px;font-weight:600;margin-bottom:12px;letter-spacing:.3px}
.foot-col li{list-style:none;line-height:26px}
.copyright{position:absolute;top:262px;width:1200px;text-align:center;font-size:10px;color:var(--footer-text);letter-spacing:.3px}
</style>
</head>
<body>

<header class="site-header">
  <div class="brand"><span class="dot"></span>Birch And Harbor</div>
  <nav class="main-nav">
    <a style="left:525px">Home</a>
    <a style="left:609px">About</a>
    <a style="left:690px">Our Process</a>
    <a style="left:806px">Blog</a>
    <a style="left:872px">Resources</a>
    <a style="left:977px">Contact</a>
  </nav>
</header>

<section class="hero" role="img" aria-label="Wooden desk with a vintage typewriter, notebooks, a coffee cup and a plant">
  <div class="hero-panel">
    <h1>NEED HELP<br>PUBLISHING<br>A BESTSELLER?</h1>
    <div class="btn-outline">FIND OUT MORE</div>
  </div>
  <div class="hero-arrow" style="left:36px"></div>
  <div class="hero-arrow" style="left:1126px"></div>
  <div class="hero-dots"><span></span><span></span><span class="on"></span><span></span></div>
</section>

<p class="intro">Our <span class="accent">proofreading, editing</span> and manuscript review packages are specifically tailored to help you publish the best possible version of your story.</p>
<div class="ornament" style="top:841px" role="img" aria-label="Red heart and swirl section divider ornament"></div>
<div class="rule"></div>

<h2 class="services-title"><span class="accent">OUR</span> SERVICES</h2>
<p class="services-lead">We've carefully structured our packages to maximize value for every budget.</p>

<div class="service-card" style="left:462px;top:998px">
  <svg viewBox="0 0 64 64"><rect x="16" y="8" width="32" height="44" rx="2" fill="#e3101c"/><rect x="16" y="48" width="32" height="8" fill="#1b1b1b"/><rect x="22" y="16" width="20" height="3" fill="#fff"/></svg>
  <p>Spelling and<br>word choice <span class="accent">issues</span></p>
</div>
<div class="service-card" style="left:761px;top:998px">
  <svg viewBox="0 0 64 64"><circle cx="32" cy="26" r="14" fill="none" stroke="#1b1b1b" stroke-width="3"/><rect x="26" y="40" width="12" height="10" fill="#e3101c"/><path d="M32 4v4M12 26h-4M56 26h-4M17 11l3 3M47 11l-3 3" stroke="#1b1b1b" stroke-width="3"/></svg>
  <p>Punctuation<br>and <span class="accent">style</span></p>
</div>
<div class="service-card" style="left:163px;top:1236px">
  <svg viewBox="0 0 64 64"><rect x="14" y="10" width="30" height="44" fill="#e3101c"/><rect x="20" y="18" width="18" height="12" fill="#fff"/><rect x="48" y="10" width="6" height="38" fill="#1b1b1b"/><path d="M48 48 L51 56 L54 48Z" fill="#1b1b1b"/></svg>
  <p>Typos and<br>grammatical <span class="accent">errors.</span></p>
</div>
<div class="service-card" style="left:462px;top:1236px">
  <svg viewBox="0 0 64 64"><path d="M10 14h28M10 22h32M10 30h32M10 38h32M10 46h24" stroke="#1b1b1b" stroke-width="3"/><rect x="48" y="8" width="6" height="40" fill="#e3101c"/><path d="M48 48 L51 56 L54 48Z" fill="#1b1b1b"/></svg>
  <p>Word choice,<br>clarity and <span class="accent">flow.</span></p>
</div>
<div class="service-card" style="left:761px;top:1236px">
  <svg viewBox="0 0 64 64"><rect x="12" y="32" width="22" height="22" rx="3" fill="#e3101c"/><rect x="18" y="26" width="10" height="6" fill="#1b1b1b"/><path d="M52 6 L36 40 L40 42 L56 8Z" fill="none" stroke="#1b1b1b" stroke-width="3"/></svg>
  <p>Sentence<br>structure and <span class="accent">craft</span></p>
</div>

<section class="pricing" role="img" aria-label="Soft grey backdrop of scattered printed letters and an open book">
  <h2>PRICING</h2>
  <div class="plan" style="left:202px">
    <div class="plan-head"><div class="plan-price">$.02</div><div class="plan-unit">PER WORD</div></div>
    <ul><li>Proofreading</li><li>Line Edit (Copy-editing)</li><li>Fix spelling and grammar</li><li>Sales copy/summary revision</li></ul>
    <div class="btn-red">GET STARTED</div>
  </div>
  <div class="plan" style="left:473px">
    <div class="plan-head"><div class="plan-price">$.04</div><div class="plan-unit">PER WORD</div></div>
    <ul><li>Proofreading</li><li>Line Edit (Copy-editing)</li><li>Fix spelling and grammar</li><li>Sales copy/summary revision</li><li>Organization and content</li><li>Plot and pacing</li><li>Manuscript Review</li></ul>
    <div class="btn-red">GET STARTED</div>
  </div>
  <div class="plan" style="left:748px">
    <div class="plan-head"><div class="plan-price">$.06</div><div class="plan-unit">PER WORD</div></div>
    <ul><li>Proofreading</li><li>Line Edit (Copy-editing)</li><li>Fix spelling and grammar</li><li>Sales copy/summary revision</li><li>Organization and content</li><li>Plot and pacing</li><li>Manuscript Review</li><li>Formatting (print and ebook)</li><li>Pre-publication proofread</li></ul>
    <div class="btn-red">GET STARTED</div>
  </div>
</section>

<h2 class="how-title"><span class="accent">HOW DOES</span> IT WORK?</h2>
<div class="step" style="left:163px">
  <div class="step-photo" role="img" aria-label="Writer working on a manuscript at a desk" style="background:linear-gradient(135deg,#2e2a27,#8a7a6a 60%,#d8d0c6)"></div>
  <h3>1. Tell Us About Your Book</h3>
  <p>Sed ut perspiciatis unde omnisillup tem accusantium doloremque uotem aperiam, eaqueueeab illo inv.</p>
</div>
<div class="step" style="left:463px">
  <div class="step-photo" role="img" aria-label="Editor typing on a laptop" style="background:linear-gradient(135deg,#1f2326,#5b6468 55%,#b9bec0)"></div>
  <h3>2. Get Your Ideal Editor</h3>
  <p>Sed ut perspiciatis unde omnisillup tem accusantium doloremque uotem aperiam, eaqueueeab illo inv.</p>
</div>
<div class="step" style="left:764px">
  <div class="step-photo" role="img" aria-label="Stack of open books" style="background:linear-gradient(135deg,#7a5b3a,#c9a87a 55%,#efe3cc)"></div>
  <h3>3. Get A Trial Edit</h3>
  <p>Sed ut perspiciatis unde omnisillup tem accusantium doloremque uotem aperiam, eaqueueeab illo inv.</p>
</div>
<div class="ornament" style="top:2899px" role="img" aria-label="Red heart and swirl section divider ornament"></div>

<div class="process-frame"></div>
<div class="process-photo" role="img" aria-label="Hands typing on a laptop beside a cup of coffee"></div>
<h2 class="process-title"><span class="accent">OUR</span> PROCESS</h2>
<div class="process-copy">
  <p>Send us a sample of your book. Our caffeine-fueled, eagle-eyed editors will go through it and then email you with their comments and suggestions. You can ask them any questions you want.</p>
  <p>If your writing is already clean, then they’ll discuss bigger picture things with you, like theme, concept, purpose, audience, potential market and branding (including title, subtitle, and tagline or elevator pitch).</p>
  <p>Once you feel comfortable and confident in an editor’s expertise, skill and knowledge, and are ready to move ahead, we’ll send an invoice for the first half of the total word count so the editor can get started. We’ll charge the rest when the project is close to completion.</p>
</div>

<div class="call-band">
  <svg width="26" height="26" viewBox="0 0 24 24"><path d="M6.6 10.8a15 15 0 0 0 6.6 6.6l2.2-2.2c.3-.3.7-.4 1-.2 1.1.4 2.3.6 3.6.6.6 0 1 .4 1 1V20c0 .6-.4 1-1 1A17 17 0 0 1 3 4c0-.6.4-1 1-1h3.5c.6 0 1 .4 1 1 0 1.3.2 2.5.6 3.6.1.3 0 .7-.2 1z" fill="none" stroke="#fff" stroke-width="1.6"/></svg>
  Call us on 000 555 0192
</div>

<footer class="site-footer">
  <div class="brand"><span class="dot"></span>Birch And Harbor</div>
  <div class="social"><span></span><span></span><span></span><span></span></div>
  <div class="foot-col" style="left:373px"><h4>INFORMATION</h4><ul><li>Perspiciatis unde</li><li>Perspiciatis unde</li><li>Sed uerspiciatism</li><li>Commolesetu</li></ul></div>
  <div class="foot-col" style="left:557px"><h4>WHO WE ARE</h4><ul><li>Sed uterspiciatis</li><li>Perspiciatis unde</li><li>Perspiciatis unde</li><li>Sed uerspiciatie</li></ul></div>
  <div class="foot-col" style="left:727px"><h4>POLICIES</h4><ul><li>Privacy</li><li>Complaint and Feedback</li></ul></div>
  <div class="foot-col" style="left:924px"><h4>OTHER LINKS</h4><ul><li>Sed uterspiciatis</li><li>Perspiciatis unde</li><li>Perspiciatis unde</li><li>Sed uerspicia</li></ul></div>
  <p class="copyright">© 2018 BIRCH AND HARBOR. PRIVACY POLICY &nbsp;|&nbsp; TERMS OF USE &nbsp;|&nbsp; CONTACT</p>
</footer>

</body>
</html>
```